TALMORK

The business want a professional looking business card. We have a scetch we will add but want the extra upgrade, and would like more suggestions for variations of our business cards.

```html
<!DOCTYPE html>
<html lang="en">
<head>
<meta charset="utf-8">
<title>TALMORK — Business Card</title>
<link href="https://fonts.googleapis.com/css2?family=Arimo:wght@400&display=swap" rel="stylesheet">
<style>
  :root {
    --stage: #3d3d3d;
    --card-light: #ffffff;
    --card-dark: #2f2f2f;
    --gold: #b08a45;
    --gold-soft: #c49a56;
    --bronze-deep: #5b3411;
    --ink-grey: #6b6b6b;
    --white: #ffffff;
  }
  * { margin: 0; padding: 0; box-sizing: border-box; }
  html, body {
    width: 1200px; height: 1200px; overflow: hidden;
    background: var(--stage);
    font-family: "Arimo", Arial, sans-serif;
  }
  .card {
    position: absolute;
    width: 689px; height: 393px;
    border-radius: 25px;
    overflow: hidden;
    box-shadow: 0 6px 18px rgba(0,0,0,0.35);
  }
  .card--front { left: 266px; top: 158px; background: var(--card-light); }
  .card--back  { left: 262px; top: 652px; background: var(--card-dark); }

  .front-wave { position: absolute; inset: 0; width: 100%; height: 100%; }

  .brand-mark {
    position: absolute;
    left: 44px; top: 118px; width: 198px;
    display: flex; flex-direction: column; align-items: center; gap: 18px;
  }
  .brand-dot {
    width: 34px; height: 34px; border-radius: 50%;
    background: var(--gold);
  }
  .brand-name {
    color: var(--gold);
    font-size: 26px;
    letter-spacing: 9px;
    margin-right: -9px;
    line-height: 1;
  }

  .holder { position: absolute; left: 44px; top: 239px; }
  .holder-name { color: var(--gold); font-size: 21px; line-height: 1.2; }
  .holder-role { color: var(--ink-grey); font-size: 15.5px; margin-top: 9px; }

  .contact {
    position: absolute; right: 39px; top: 300px;
    text-align: right; color: var(--white);
    font-size: 16px; line-height: 21px;
  }
  .contact-web { letter-spacing: 1.6px; }

  .back-mark {
    position: absolute; left: 0; right: 0; top: 120px;
    display: flex; flex-direction: column; align-items: center; gap: 20px;
  }
  .back-mark .brand-dot { width: 46px; height: 46px; }
  .back-mark .brand-name { font-size: 34px; letter-spacing: 12px; margin-right: -12px; }
  .back-web {
    position: absolute; left: 0; right: 0; top: 302px;
    text-align: center; color: var(--white);
    font-size: 16px; letter-spacing: 2px;
  }
</style>
</head>
<body>
  <section class="card card--front">
    <svg class="front-wave" viewBox="0 0 1109 633" preserveAspectRatio="none" aria-hidden="true">
      <defs>
        <linearGradient id="bronzeSweep" x1="0" y1="0" x2="1" y2="0">
          <stop offset="0" stop-color="#5b3411"/>
          <stop offset="0.3" stop-color="#8d6229"/>
          <stop offset="0.58" stop-color="#c49a56"/>
          <stop offset="0.8" stop-color="#8e5f27"/>
          <stop offset="1" stop-color="#5e3510"/>
        </linearGradient>
      </defs>
      <path d="M0,518 C190,572 400,585 610,530 C850,465 1000,300 1109,58 L1109,633 L0,633 Z" fill="url(#bronzeSweep)"/>
      <path d="M0,546 C200,578 420,582 620,532 C860,462 1000,330 1109,108" fill="none" stroke="#ffffff" stroke-width="2"/>
    </svg>

    <div class="brand-mark">
      <span class="brand-dot"></span>
      <span class="brand-name">TALMORK</span>
    </div>

    <div class="holder">
      <p class="holder-name">Henrik Aasvold Strand</p>
      <p class="holder-role">CEO &amp; Founder</p>
    </div>

    <div class="contact">
      <p>004790012345</p>
      <p>talmork.llc@mailbox.com</p>
      <p class="contact-web">www.talmork.llc</p>
    </div>
  </section>

  <section class="card card--back">
    <div class="back-mark">
      <span class="brand-dot"></span>
      <span class="brand-name">TALMORK</span>
    </div>
    <p class="back-web">www.talmork.llc</p>
  </section>
</body>
</html>
```